KRV Cartridge chip board folding ammuniton boxes for retail sale

Design a scalable design for use with 20 round and 50 round boxes for Ammunition. The caliber will be 9mm but will need to be editable, all warnings and barcodes will need to be able to be edited also. I have attached the company logo.

**UPDATE**
Box dimensions
20rd= 2.55in long X 2.1in width X 1.25in height

50rd= 5.1in long x 2.6in width X 1.2in height

Please see the bullet picture i would like used if possible.

Target Market(s)

Quality shooting sports, self defense

Industry/Entity Type

Self Defense

Requirements
Must have
• supplied company logo design
Should not have
• any cartoons of any kind

```html
<!DOCTYPE html>
<html lang="en">
<head>
<meta charset="utf-8">
<title>KRV Cartridge – 9mm FMJ 50 Round Box</title>
<link href="https://fonts.googleapis.com/css2?family=Exo+2:wght@800&family=Roboto+Condensed:wght@400;500&display=swap" rel="stylesheet">
<style>
  :root {
    --stage: #d91c22;
    --panel-white: #f7f7f7;
    --ink: #1c1c1c;
    --brand-red: #e0262b;
    --side-dark: #141414;
    --side-mid: #2a2a2a;
    --brass-light: #e6c77d;
    --brass-dark: #a67a33;
    --copper: #c0714a;
    --text-light: #f2f2f2;
  }
  * { box-sizing: border-box; margin: 0; padding: 0; }
  html, body { width: 1200px; height: 840px; overflow: hidden; }
  body {
    background: var(--stage);
    position: relative;
    font-family: "Roboto Condensed", sans-serif;
  }
  .box-net { position: absolute; inset: 0; }

  /* Top face */
  .top-face {
    position: absolute; left: 430px; top: 80px; width: 700px; height: 357px;
    background: var(--panel-white);
  }
  .brand-lockup { position: absolute; left: 60px; top: 56px; }
  .brand-mark-row { display: flex; align-items: center; gap: 18px; }
  .brand-initials {
    font-family: "Exo 2", sans-serif; font-weight: 800; font-size: 96px;
    line-height: 1; color: var(--ink); letter-spacing: 4px;
  }
  .brand-dot {
    width: 64px; height: 64px; border-radius: 50%;
    background: var(--brand-red);
  }
  .brand-name {
    font-family: "Exo 2", sans-serif; font-weight: 800; font-size: 30px;
    line-height: 1.1; color: var(--ink); margin-top: 6px;
  }
  .rounds-photo {
    position: absolute; right: 40px; top: 70px; width: 210px; height: 150px;
    border-radius: 12px;
    background: linear-gradient(135deg, var(--copper), var(--brass-light) 55%, var(--brass-dark));
  }
  .load-label { position: absolute; left: 50px; bottom: 30px; width: 250px; height: 100px; }
  .load-label svg { display: block; }
  .load-text {
    position: absolute; left: 20px; top: 16px; color: var(--text-light);
    font-size: 27px; line-height: 1.05; font-weight: 500;
  }

  /* Front side */
  .front-side {
    position: absolute; left: 430px; top: 437px; width: 700px; height: 164px;
    background: linear-gradient(100deg, var(--side-dark), var(--side-mid) 50%, var(--side-dark));
    display: flex; align-items: center; justify-content: space-between; padding: 0 36px;
  }
  .side-brand { display: flex; align-items: center; gap: 16px; }
  .side-initials {
    font-family: "Exo 2", sans-serif; font-weight: 800; font-size: 66px;
    color: var(--brand-red); line-height: 1;
  }
  .side-name {
    font-family: "Exo 2", sans-serif; font-weight: 800; font-size: 20px;
    color: var(--brand-red); margin-top: 4px;
  }
  .side-dot { width: 40px; height: 40px; border-radius: 50%; background: var(--brand-red); }
  .caliber-block { display: flex; align-items: center; gap: 22px; }
  .round-photo {
    width: 34px; height: 110px; border-radius: 14px 14px 3px 3px;
    background: linear-gradient(180deg, var(--copper) 0 30%, var(--brass-light) 30%, var(--brass-dark));
  }
  .caliber-text { font-weight: 500; color: var(--text-light); line-height: 1; }
  .caliber-type { font-size: 40px; }
  .caliber-size { font-size: 58px; }

  /* End panel */
  .end-panel {
    position: absolute; left: 73px; top: 437px; width: 357px; height: 164px;
    background: linear-gradient(90deg, var(--side-dark), var(--side-mid));
    padding: 22px 26px;
  }
  .lead-warning { color: var(--text-light); font-size: 14px; line-height: 1.4; opacity: .85; }
</style>
</head>
<body>
<main class="box-net">
  <section class="top-face">
    <div class="brand-lockup">
      <div class="brand-mark-row">
        <span class="brand-initials">KRV</span>
        <span class="brand-dot"></span>
      </div>
      <div class="brand-name">Kestrel Ridge Cartridge</div>
    </div>
    <div class="rounds-photo" role="img" aria-label="Photograph of loose 9mm full metal jacket cartridges"></div>
    <div class="load-label">
      <svg width="250" height="100" viewBox="0 0 250 100">
        <path d="M0 0 H150 A100 50 0 0 1 150 100 H0 Z" fill="#000"/>
        <line x1="145" y1="0" x2="145" y2="100" stroke="#f7f7f7" stroke-width="3"/>
      </svg>
      <div class="load-text">9mm FMJ<br>50 ROUND</div>
    </div>
  </section>

  <section class="front-side">
    <div class="side-brand">
      <div>
        <div class="side-initials">KRV</div>
        <div class="side-name">Kestrel Ridge Cartridge</div>
      </div>
      <span class="side-dot"></span>
    </div>
    <div class="caliber-block">
      <div class="round-photo" role="img" aria-label="Photograph of a single 9mm cartridge"></div>
      <div class="caliber-text">
        <div class="caliber-type">FMG</div>
        <div class="caliber-size">9mm</div>
      </div>
    </div>
  </section>

  <section class="end-panel">
    <p class="lead-warning">LEAD WARNING: Discharging firearms in poorly ventilated areas, cleaning firearms or handling ammunition may result in exposure to lead. Wash hands thoroughly after exposure.</p>
  </section>
</main>
</body>
</html>
```